Business card design Needed for new logo / Construction business, home extensions and new builds

We need a business card design using our new logo files which i will attach to this project :)

We are a small construction business specialising in home extensions, new builds and property development. We are very ambitious and would appreciate professional and elegant designs for our new business card.

Very serious about using the services on MakerQuarry and recently acquired our new logo from here :)

Please get involved, i will feedback when i can as i am very busy but can respond daily, thanks

Target Market(s)

People that want to build onto their houses, new building developments or adding too their existing property

Industry/Entity Type

Construction

Contact Information for Business Card

Renwick Tolliver Construction, Lionel Ashby (Managing Director), Tel 07822254961, email - info@renwick-tolliver, www.renwick-tolliver.co.uk

Colors

Designer to choose colors to be used in the design.

Requirements
Must have
• I like a deep grey on the back please. A lot of you have provided black from and back, try mixing things up a little. The black looks cool 😎 Thanks

```html
<!DOCTYPE html>
<html lang="en">
<head>
<meta charset="utf-8">
<title>Renwick Tolliver Construction – Business Card</title>
<link href="https://fonts.googleapis.com/css2?family=Cinzel:wght@500;600&family=EB+Garamond:wght@400;500&display=swap" rel="stylesheet">
<style>
  :root {
    --backdrop: #d9d9d9;
    --card-black: #0b0b0b;
    --card-deep: #161616;
    --card-edge: #1f1f1f;
    --gold: #d4a63c;
    --gold-soft: #c8982f;
    --silver: #cfcfcf;
    --text-light: #e6e6e6;
    --rule: #6a6a6a;
  }
  * { margin: 0; padding: 0; box-sizing: border-box; }
  html, body { width: 1200px; height: 900px; overflow: hidden; }
  body {
    background: var(--backdrop);
    display: flex;
    flex-direction: column;
    align-items: center;
    justify-content: center;
    gap: 40px;
  }
  .card {
    width: 700px;
    height: 400px;
    border-radius: 34px;
    position: relative;
    overflow: hidden;
    box-shadow: 0 10px 24px rgba(0,0,0,0.25);
  }

  /* Back side */
  .card--back { background: var(--card-deep); }
  .card__pattern {
    position: absolute; inset: 0;
    background: radial-gradient(ellipse at 55% 45%, #2a2a2a 0%, #181818 55%, #0e0e0e 100%);
  }
  .card__corner-name {
    position: absolute;
    right: 58px;
    top: 150px;
    font-family: "Cinzel", serif;
    font-weight: 600;
    font-size: 15px;
    letter-spacing: 1px;
    color: var(--gold);
  }

  /* Front side */
  .card--front { background: var(--card-black); display: flex; }
  .card__brand {
    width: 47%;
    display: flex;
    flex-direction: column;
    align-items: center;
    justify-content: center;
    gap: 14px;
    padding-top: 40px;
  }
  .brand__square {
    width: 22px; height: 22px;
    background: var(--gold);
  }
  .brand__name {
    font-family: "Cinzel", serif;
    font-weight: 600;
    font-size: 24px;
    line-height: 1.3;
    text-align: center;
    letter-spacing: 1px;
    color: var(--gold);
  }
  .card__divider {
    width: 1px;
    background: var(--rule);
    margin: 70px 0 80px;
  }
  .card__details {
    flex: 1;
    padding: 90px 0 0 40px;
    font-family: "EB Garamond", serif;
    color: var(--text-light);
  }
  .person__name {
    font-family: "EB Garamond", serif;
    font-weight: 500;
    font-size: 21px;
    letter-spacing: 1px;
    color: var(--gold);
    text-transform: uppercase;
  }
  .person__role { font-size: 16px; margin-top: 2px; }
  .person__phone-lead { font-size: 17px; margin-top: 14px; }
  .contact-list { list-style: none; margin-top: 18px; }
  .contact-list li {
    display: flex; align-items: center; gap: 10px;
    font-size: 16px; margin-bottom: 10px;
  }
  .contact-icon { width: 18px; height: 18px; flex: none; }
</style>
</head>
<body>

  <section class="card card--back" aria-label="Card back">
    <div class="card__pattern" role="img" aria-label="Repeating faint embossed monogram pattern on deep grey"></div>
    <span class="card__corner-name">Renwick Tolliver</span>
  </section>

  <section class="card card--front" aria-label="Card front">
    <div class="card__brand">
      <span class="brand__square"></span>
      <span class="brand__name">Renwick Tolliver<br>Construction</span>
    </div>
    <div class="card__divider"></div>
    <div class="card__details">
      <p class="person__name">Lionel Ashby</p>
      <p class="person__role">Managing Director</p>
      <p class="person__phone-lead">07822254961</p>
      <ul class="contact-list">
        <li>
          <svg class="contact-icon" viewBox="0 0 18 18" aria-hidden="true">
            <path d="M4 2h3l1.5 4-2 1.3a9 9 0 0 0 4.2 4.2L12 9.5l4 1.5v3a2 2 0 0 1-2 2A13 13 0 0 1 2 4a2 2 0 0 1 2-2z" fill="var(--gold)"/>
          </svg>
          07822254961
        </li>
        <li>
          <svg class="contact-icon" viewBox="0 0 18 18" aria-hidden="true">
            <rect x="1.5" y="4" width="15" height="10" rx="1.5" fill="var(--gold)"/>
            <path d="M2 5l7 5 7-5" fill="none" stroke="var(--card-black)" stroke-width="1.3"/>
          </svg>
          info@renwick-tolliver.co.uk
        </li>
        <li>
          <svg class="contact-icon" viewBox="0 0 18 18" aria-hidden="true">
            <circle cx="9" cy="9" r="7.5" fill="none" stroke="var(--gold)" stroke-width="1.5"/>
            <ellipse cx="9" cy="9" rx="3" ry="7.5" fill="none" stroke="var(--gold)" stroke-width="1.2"/>
            <path d="M1.5 9h15" stroke="var(--gold)" stroke-width="1.2"/>
          </svg>
          www.renwick-tolliver.co.uk
        </li>
      </ul>
    </div>
  </section>

</body>
</html>
```